Bright Harbor Counseling Letterhead for hip modern business

I would like some ombre use of the colors in the logo hip letterhead that incorporates logo colors and feel, needs to connect with young professionals and college students. i need to be able to write letters to schools to excuse absences as well. i like color blocks on one side preferably using colors from the attached logo design.

Target Market(s)

high income young people, young adults and college students

Industry/Entity Type

mental health

Font styles to use
Serif
Sans Serif

Colors
0054AA
0677BA
7BADD7
CADEEF
E8F1F8
0094D4
00A9DD
6FCCEA
C7EBF8
E9F6FB
00AB8E
00BBA5
67D7C9
C6EFE9
E9F9F6
59FF00
82FF00
B8FF75
E3FFCB
F4FFEA
A7469A
B969AE
D3A5CF
EDDBEB
F8F0F9
6B429C
8869AF
B7A5CE
E3DAEB
F3F0F8

Requirements
Must have
• a modern hip feel, somewhat color

```html
<!DOCTYPE html>
<html lang="en">
<head>
<meta charset="utf-8">
<title>Bright Harbor Counseling Letterhead</title>
<link rel="stylesheet" href="https://fonts.googleapis.com/css2?family=Arimo:wght@400;700&family=Homemade+Apple&display=swap">
<style>
  :root {
    --backdrop: #2e2e2e;
    --paper: #ffffff;
    --ink: #4a4a4a;
    --brand-blue: #2f74c0;
    --brand-purple: #93337f;
    --brand-teal: #4fc4b3;
    --watermark: #ece4f1;
    --on-dark: #ffffff;
  }
  * { margin: 0; padding: 0; box-sizing: border-box; }
  html, body {
    width: 1200px; height: 962px; overflow: hidden;
    background: var(--backdrop);
  }
  .letterhead {
    position: absolute; left: 282px; top: 31px;
    width: 636px; height: 900px;
    background: var(--paper);
    font-family: "Arimo", Arial, sans-serif;
    color: var(--ink);
    overflow: hidden;
  }
  .decor { position: absolute; inset: 0; }
  .website {
    position: absolute; top: 46px; right: 34px;
    font-size: 10px; font-weight: 700; color: var(--brand-blue);
    letter-spacing: 0.2px;
  }
  .brand {
    position: absolute; left: 40px; top: 120px;
    display: flex; align-items: center; gap: 10px;
  }
  .brand-dot {
    width: 22px; height: 22px; border-radius: 50%;
    background: var(--brand-purple);
  }
  .brand-name {
    font-size: 19px; font-weight: 400; color: var(--ink);
    line-height: 1.1;
  }
  .letter {
    position: absolute; left: 40px; top: 262px; width: 556px;
    font-size: 11px; line-height: 1.3;
  }
  .date { margin-bottom: 12px; }
  .recipient { margin-bottom: 14px; }
  .salutation { font-weight: 700; font-size: 12px; margin-bottom: 10px; }
  .body { margin-bottom: 10px; }
  .signoff {
    margin: 14px 0 0 390px;
    font-size: 11px; line-height: 1.35;
  }
  .signature {
    font-family: "Homemade Apple", cursive;
    font-size: 17px; line-height: 1.5; color: #6b6b6b;
    margin: 2px 0 2px -24px;
  }
  .contact {
    position: absolute; right: 30px; top: 800px;
    list-style: none; text-align: right;
    font-size: 10px; line-height: 1.6; color: var(--on-dark);
  }
  .contact li { display: flex; justify-content: flex-end; align-items: center; gap: 6px; }
  .contact svg { width: 11px; height: 11px; flex: none; }
</style>
</head>
<body>
  <main class="letterhead">
    <svg class="decor" viewBox="0 0 636 900" aria-hidden="true">
      <path d="M15 236 C 140 224, 225 172, 285 112 S 395 14, 470 0 L 500 0 C 420 22, 345 80, 300 124 S 160 230, 15 236 Z" fill="var(--brand-blue)"/>
      <circle cx="318" cy="300" r="72" fill="var(--watermark)" opacity="0.7"/>
      <path d="M150 900 C 300 865, 365 790, 435 725 S 570 640, 636 622 L636 638 C 580 652, 512 695, 452 742 S 300 880, 172 900 Z" fill="var(--brand-teal)"/>
      <path d="M192 900 C 320 868, 385 800, 460 750 S 585 665, 636 652 L636 900 Z" fill="var(--brand-purple)"/>
    </svg>

    <div class="website">www.brightharborcounseling.com</div>

    <div class="brand">
      <span class="brand-dot"></span>
      <span class="brand-name">Bright Harbor<br>Counseling</span>
    </div>

    <section class="letter">
      <p class="date">January 12, 2021</p>
      <p class="recipient">Mr. John Doe<br>President<br>AA Corporation<br>111 Street Name, Suite#<br>City, State, 12345</p>
      <p class="salutation">Dear Mr. John,</p>
      <p class="body">Lorem Ipsum is simply dummy text of the printing and typesetting industry. Lorem Ipsum has been the industry's standard dummy text ever since the 1500s, when an unknown printer took a galley of type and scrambled it to make a type specimen book. It has survived not only five centuries, but also the leap into electronic typesetting, remaining essentially unchanged.</p>
      <p class="body">The standard chunk of Lorem Ipsum used since the 1500s is reproduced below for those interested. Sections 1.10.32 and 1.10.33 from "de Finibus Bonorum et Malorum" by Cicero are also reproduced in their exact original form, accompanied by English versions from the 1914 translation by H. Rackham</p>
      <p class="body">Lorem Ipsum is simply dummy text of the printing and typesetting industry. Lorem Ipsum has been the industry's standard dummy text ever since the 1500s, when an unknown printer took a galley of type and scrambled it to make a type specimen book. It has survived not only five centuries, but also the leap into electronic typesetting, remaining essentially unchanged. It was popularised in the</p>
      <div class="signoff">
        <p>Sincerely Your,</p>
        <p class="signature">your name</p>
        <p>Name Last Name<br>Company Name</p>
      </div>
    </section>

    <ul class="contact">
      <li>(00) 05550 214 386
        <svg viewBox="0 0 12 12"><circle cx="6" cy="6" r="6" fill="var(--brand-blue)"/><path d="M4 3 L5.2 3 L5.6 4.6 L4.9 5.2 Q5.6 6.6 6.8 7.1 L7.4 6.4 L9 6.8 L9 8 Q5 8.6 3.4 4.2 Z" fill="#fff"/></svg></li>
      <li>(00) 05550 214 387
        <svg viewBox="0 0 12 12"><circle cx="6" cy="6" r="6" fill="var(--brand-blue)"/><path d="M4 3 L5.2 3 L5.6 4.6 L4.9 5.2 Q5.6 6.6 6.8 7.1 L7.4 6.4 L9 6.8 L9 8 Q5 8.6 3.4 4.2 Z" fill="#fff"/></svg></li>
      <li>hello@brightharborcounseling.com
        <svg viewBox="0 0 12 12"><circle cx="6" cy="6" r="6" fill="var(--brand-blue)"/><rect x="3" y="4" width="6" height="4.2" fill="#fff"/><path d="M3 4 L6 6.4 L9 4" fill="none" stroke="var(--brand-blue)" stroke-width="0.7"/></svg></li>
      <li>Suite 48 Harbor Lane, State, Zip 5021, Country
        <svg viewBox="0 0 12 12"><circle cx="6" cy="6" r="6" fill="var(--brand-blue)"/><path d="M6 2.6 A2.2 2.2 0 0 1 8.2 4.8 Q8.2 6.4 6 9.4 Q3.8 6.4 3.8 4.8 A2.2 2.2 0 0 1 6 2.6 Z" fill="#fff"/><circle cx="6" cy="4.8" r="0.8" fill="var(--brand-blue)"/></svg></li>
    </ul>
  </main>
</body>
</html>
```